RWT Fittings Ltd Business Cards

We need a business card with our business logo. We provide window and door installations on high-rises in west coast British Colombia, Canada.

I would like my business information and details on one side of the card, and the other side the company name with logo

Target Market(s)

General Contractors

Industry/Entity Type

Construction

Contact Information for Business Card

one side i want my company name and logo in the dark theme logo that i provided

Requirements
Must have
• Marco Peltieri, 16045518293, RWTFittings@mailbox-demo.com, 1407-5194 Linden Row Burnaby BC, V5H 2K9, Owner & Manager

```html
<!DOCTYPE html>
<html lang="en">
<head>
<meta charset="utf-8">
<title>RWT Fittings Ltd – Business Cards</title>
<link rel="stylesheet" href="https://fonts.googleapis.com/css2?family=Poppins:wght@300;400;700&display=swap">
<style>
  :root {
    --page-bg: #e6e6e4;
    --card-white: #ffffff;
    --brand-blue: #1ea7e1;
    --text-grey: #6d6d6d;
    --dark-card-a: #2b2927;
    --dark-card-b: #4a4541;
    --logo-cyan: #2fc3f2;
  }
  * { box-sizing: border-box; margin: 0; padding: 0; }
  html, body { width: 1200px; height: 963px; overflow: hidden; }
  body {
    background: var(--page-bg);
    font-family: "Poppins", sans-serif;
    position: relative;
  }
  .card {
    position: absolute;
    top: 330px;
    width: 530px;
    height: 303px;
    border-radius: 14px;
    overflow: hidden;
    box-shadow: 0 10px 30px rgba(0,0,0,0.18);
  }
  /* Front side */
  .card-front { left: 45px; background: var(--card-white); }
  .contact-block { position: absolute; left: 36px; top: 92px; }
  .person-name {
    color: var(--brand-blue);
    font-weight: 700;
    font-size: 22px;
    letter-spacing: 0.5px;
    text-transform: uppercase;
    line-height: 1.1;
  }
  .person-title {
    color: var(--text-grey);
    font-weight: 300;
    font-size: 12px;
    margin-bottom: 12px;
  }
  .contact-line {
    display: flex;
    align-items: center;
    gap: 7px;
    color: var(--text-grey);
    font-weight: 400;
    font-size: 12.5px;
    line-height: 1.55;
  }
  .contact-line svg { width: 11px; height: 11px; flex: none; }
  .front-brand {
    position: absolute;
    right: 34px;
    top: 98px;
    display: flex;
    align-items: center;
    gap: 10px;
  }
  .brand-square { width: 26px; height: 26px; background: var(--brand-blue); }
  .brand-name {
    color: var(--brand-blue);
    font-weight: 700;
    font-size: 24px;
    line-height: 1;
    white-space: nowrap;
  }
  .address {
    position: absolute;
    right: 34px;
    bottom: 30px;
    color: var(--text-grey);
    font-weight: 300;
    font-size: 12.5px;
    line-height: 1.45;
    text-align: right;
  }
  .accent-bar {
    position: absolute;
    left: 226px;
    bottom: 0;
    width: 108px;
    height: 14px;
    background: var(--brand-blue);
  }
  /* Back side */
  .card-back {
    left: 625px;
    background: linear-gradient(135deg, var(--dark-card-a) 0%, var(--dark-card-a) 40%, var(--dark-card-b) 100%);
    display: flex;
    align-items: center;
    justify-content: center;
  }
  .back-brand { display: flex; align-items: center; gap: 12px; }
  .back-brand .brand-square { width: 32px; height: 32px; background: var(--logo-cyan); }
  .back-brand .brand-name { color: var(--logo-cyan); font-size: 32px; }
</style>
</head>
<body>
  <section class="card card-front" aria-label="Business card front">
    <div class="contact-block">
      <p class="person-name">Marco Peltieri</p>
      <p class="person-title">Owner &amp; Manager</p>
      <p class="contact-line">
        <svg viewBox="0 0 12 12" aria-hidden="true"><path d="M2.5 1 L4.5 1 L5.2 3.6 L4 4.6 Q5 7 7.4 8 L8.4 6.8 L11 7.5 L11 9.5 Q10.5 11 9 11 Q1 10 1 3 Q1 1.5 2.5 1 Z" fill="var(--brand-blue)"/></svg>
        16045518293
      </p>
      <p class="contact-line">
        <svg viewBox="0 0 12 12" aria-hidden="true"><rect x="0.8" y="2.3" width="10.4" height="7.4" rx="1" fill="none" stroke="var(--brand-blue)" stroke-width="1.1"/><path d="M1 2.8 L6 6.6 L11 2.8" fill="none" stroke="var(--brand-blue)" stroke-width="1.1"/></svg>
        RWTFittings@mailbox-demo.com
      </p>
      <p class="contact-line">
        <svg viewBox="0 0 12 12" aria-hidden="true"><circle cx="6" cy="6" r="5" fill="none" stroke="var(--brand-blue)" stroke-width="1.1"/><ellipse cx="6" cy="6" rx="2.2" ry="5" fill="none" stroke="var(--brand-blue)" stroke-width="1"/><path d="M1 6 H11 M2 3.5 H10 M2 8.5 H10" stroke="var(--brand-blue)" stroke-width="0.9"/></svg>
        www.rwtfittings-demo.com
      </p>
    </div>
    <div class="front-brand">
      <span class="brand-square" aria-hidden="true"></span>
      <span class="brand-name">RWT Fittings Ltd</span>
    </div>
    <p class="address">1407-5194 Linden Row<br>Burnaby BC, V5H 2K9</p>
    <span class="accent-bar" aria-hidden="true"></span>
  </section>

  <section class="card card-back" aria-label="Business card back">
    <div class="back-brand">
      <span class="brand-square" aria-hidden="true"></span>
      <span class="brand-name">RWT Fittings Ltd</span>
    </div>
  </section>
</body>
</html>
```